MEDICAL CLINIC LETTERHEAD

Design is a letterhead for a non-profit medical center. The name of the clinic is VITARIDGE Community Health Center. Although the full name must be included, the community health center part is more of a description and should be less visible - i attached an example of what I mean by that (ATTACHED IMAGE IS AN EXAMPLE OF FONT SIZES NOT A DESIGN IDEA). Please design something modern, cool looking and unique because I can always download free templates.
Phone, email, website and etc will be added later.

Industry/Entity Type

MEDICAL

```html
<!DOCTYPE html>
<html lang="en">
<head>
<meta charset="utf-8">
<title>VITARIDGE Community Health Center – Letterhead</title>
<link rel="stylesheet" href="https://fonts.googleapis.com/css2?family=Lato:wght@400;700&family=Montserrat:wght@500&family=Italianno&display=swap">
<style>
  :root {
    --bg: #e2e2e2;
    --paper: #fbfbfb;
    --paper-edge: #efefef;
    --navy: #1b2947;
    --gold: #b3935a;
    --ink: #3a3a3a;
    --ink-dark: #111;
  }
  * { box-sizing: border-box; margin: 0; padding: 0; }
  html, body { width: 1153px; height: 1200px; overflow: hidden; background: var(--bg); }
  .letterhead {
    position: absolute; left: 162px; top: 20px; width: 829px; height: 1160px;
    background: radial-gradient(ellipse at 50% 35%, #ffffff 0%, var(--paper) 45%, var(--paper-edge) 100%);
    box-shadow: 0 6px 24px rgba(0,0,0,.22);
    overflow: hidden;
    font-family: "Lato", sans-serif; color: var(--ink);
  }
  .brand {
    position: absolute; left: 58px; top: 86px;
    display: flex; align-items: center; gap: 10px;
  }
  .brand-dot { width: 14px; height: 14px; border-radius: 50%; background: var(--gold); }
  .brand-name {
    font-family: "Lato", sans-serif; font-weight: 700; font-size: 34px;
    letter-spacing: 1px; color: var(--navy);
  }
  .contact {
    position: absolute; left: 567px; top: 48px; height: 93px;
    border-left: 1.5px solid var(--gold); padding-left: 12px;
    font-family: "Montserrat", sans-serif; font-weight: 500; font-size: 13.5px; color: var(--ink-dark);
  }
  .contact-org { line-height: 18px; margin-top: -2px; margin-bottom: 6px; }
  .contact-row { display: flex; align-items: center; gap: 9px; line-height: 20px; }
  .contact-row svg { width: 13px; height: 13px; fill: var(--gold); flex: none; }
  .letter { position: absolute; left: 64px; top: 256px; width: 702px; font-size: 14.3px; line-height: 18.8px; }
  .letter-date { margin-bottom: 19px; font-size: 15.5px; }
  .letter-address { font-size: 15px; margin-bottom: 18px; }
  .letter-salutation { font-weight: 700; font-size: 19px; margin: 16px 0 18px; }
  .letter p.body { text-align: justify; margin-bottom: 17px; }
  .letter-closing { margin-top: 38px; font-size: 15px; }
  .letter-signature {
    font-family: "Italianno", cursive; font-size: 44px; color: #2b2b2b; margin-top: 18px; margin-left: 4px;
  }
  .footer-band { position: absolute; left: 0; bottom: 0; width: 829px; height: 126px; display: block; }
</style>
</head>
<body>
<main class="letterhead">
  <div class="brand">
    <span class="brand-dot"></span>
    <span class="brand-name">VITARIDGE</span>
  </div>

  <address class="contact">
    <p class="contact-org">VITARIDGE Community<br>Health Center</p>
    <p class="contact-row">
      <svg viewBox="0 0 16 16"><path d="M3 2h3l1.5 3.5-2 1.3a8 8 0 0 0 3.7 3.7l1.3-2L14 10v3a1 1 0 0 1-1 1A11 11 0 0 1 2 3a1 1 0 0 1 1-1z"/></svg>
      555-214-0387
    </p>
    <p class="contact-row">
      <svg viewBox="0 0 16 16"><path d="M1 3h14v10H1z M1 3l7 6 7-6" fill="none" stroke="#b3935a" stroke-width="1.6"/></svg>
      hello@vitaridge-mail.com
    </p>
    <p class="contact-row">
      <svg viewBox="0 0 16 16"><circle cx="8" cy="8" r="7"/><path d="M1 8h14M8 1c3 3 3 11 0 14M8 1c-3 3-3 11 0 14" fill="none" stroke="#fff" stroke-width="1"/></svg>
      www.vitaridge-web.com
    </p>
  </address>

  <section class="letter">
    <p class="letter-date">Feb-03-2022</p>
    <p class="letter-address">Mr, Daniel Price<br>President</p>
    <p class="letter-address">Harbor Corporation<br>123 Street Name, Suite# 10<br>City, State, 120023</p>
    <p class="letter-salutation">Dear Mr, Daniel</p>
    <p class="body">Lorem ipsum dolor sit amet, consectetur adipisicing elit, sed do eiusmod tempor incididunt ut labore et dolore magna aliqua. Ut enim ad minim veniam, quis nostrud exercitation ullamco laboris nisi ut aliquip ex ea commodo consequat. Duis aute irure dolor in reprehenderit in voluptate velit esse cillum dolore eu fugiat nulla pariatur.</p>
    <p class="body">Lorem ipsum dolor sit amet, consectetur adipisicing elit, sed do eiusmod tempor incididunt ut labore et dolore magna aliqua. Ut enim ad minim veniam, quis nostrud exercitation ullamco laboris nisi ut aliquip ex ea commodo consequat. Duis aute irure dolor in reprehenderit in voluptate velit esse cillum dolore eu fugiat nulla pariatur.</p>
    <p class="body">Lorem ipsum dolor sit amet, consectetur adipisicing elit, sed do eiusmod tempor incididunt ut labore et dolore magna aliqua. Ut enim ad minim veniam, quis nostrud exercitation ullamco laboris nisi ut aliquip ex ea commodo consequat.</p>
    <p class="body">Excepteur sint occaecat cupidatat non proident, sunt in culpa qui officia deserunt mollit anim id est laborum. re et dolore magnam aliquam quaerat voluptatem.</p>
    <p class="letter-closing">Regards</p>
    <p class="letter-signature">Laura Bennett</p>
  </section>

  <svg class="footer-band" viewBox="0 0 829 126" preserveAspectRatio="none" aria-hidden="true">
    <path d="M0 0 Q414.5 174 829 0 L829 126 L0 126 Z" fill="var(--gold)"/>
    <path d="M39 8 Q412 152 777 12 Q412 132 39 8 Z" fill="var(--navy)"/>
  </svg>
</main>
</body>
</html>
```